Korvalith Brochure Design - IT Services - Modern Design - Services List

Hi,

We are looking for a modern IT Services brochure design of between 4 - 6 pages, it must be based on a blue and white colour theme with some nice technical imagery. It would need a section about why Korvalith and a contact section at the end.

Here is some info that could be included

Target Market(s)

Medium to Large Businesses

Industry/Entity Type

Information Technology

Colors
0054AA
0677BA
7BADD7
CADEEF
E8F1F8

Requirements
Must have
• Striking technical imagery
Nice to have
• Nice Icons to list the different services sections

```html
<!DOCTYPE html>
<html lang="en">
<head>
<meta charset="utf-8">
<title>Korvalith IT Services Brochure</title>
<link href="https://fonts.googleapis.com/css2?family=Montserrat:wght@400;500;600;700;800&family=Open+Sans:wght@600&display=swap" rel="stylesheet">
<style>
:root{
  --board:#565656;
  --mount:#3d3d3d;
  --night:#12131c;
  --blue:#1480c4;
  --deep:#1656a8;
  --sky:#7badd7;
  --pale:#cadeef;
  --mist:#e8f1f8;
  --slate:#3b3f4f;
  --ink:#3a3d47;
  --white:#ffffff;
}
*{margin:0;padding:0;box-sizing:border-box}
html,body{width:1200px;height:1200px;overflow:hidden}
body{background:var(--board);font-family:"Montserrat",sans-serif;position:relative;color:var(--ink)}
.icon-defs{position:absolute;width:0;height:0;overflow:hidden}
.label{position:absolute;font-family:"Open Sans",sans-serif;font-weight:600;font-size:22px;color:var(--white);transform:translateX(-50%);top:60px;letter-spacing:.5px}
.mount{position:absolute;background:var(--mount)}
.abs{position:absolute}

/* cover spread */
.spread{position:absolute;left:278px;top:109px;width:670px;height:440px;background:var(--white);overflow:hidden}
.photo{position:absolute}
.back-photo{left:0;top:0;width:336px;height:229px;background:
  radial-gradient(ellipse 60% 30% at 45% 32%,rgba(214,130,70,.35) 0%,rgba(214,130,70,0) 70%),
  radial-gradient(ellipse 70% 40% at 50% 55%,rgba(64,150,190,.55) 0%,rgba(64,150,190,0) 70%),
  linear-gradient(180deg,#12131c 0%,#171d2a 25%,#1f3446 45%,#1c2c3a 62%,#0f131b 82%,#0b0c12 100%)}
.front-photo{left:336px;top:0;width:334px;height:300px;background:
  radial-gradient(ellipse 55% 35% at 55% 45%,rgba(120,170,240,.85) 0%,rgba(60,110,210,.5) 45%,rgba(30,60,140,0) 80%),
  radial-gradient(ellipse 80% 20% at 50% 72%,rgba(160,200,250,.45) 0%,rgba(160,200,250,0) 70%),
  linear-gradient(180deg,#12131c 0%,#161a2e 18%,#1d3470 45%,#2450b0 75%,#1e4aa0 100%)}
.get-touch{left:26px;top:180px;width:290px;color:var(--white)}
.get-touch h3{font-weight:500;font-size:9px;margin-bottom:3px}
.get-touch p{font-size:5.6px;line-height:1.5}
.contact-band{left:0;top:229px;width:336px;height:87px;background:var(--blue);color:var(--white);padding:12px 0 0 28px}
.contact-band h4{font-weight:500;font-size:7px;margin-bottom:4px}
.contact-band li{list-style:none;font-size:7px;font-weight:500;height:13px;display:flex;align-items:center;gap:5px}
.contact-band svg{width:7px;height:7px}
.follow-band{left:0;top:318px;width:336px;height:69px;background:var(--deep);color:var(--white);padding:8px 0 0 29px}
.follow-band h4{font-weight:500;font-size:7px}
.follow-band p{font-size:5.6px;margin:2px 0 3px}
.follow-band li{list-style:none;font-size:6px;height:11px;display:flex;align-items:center;gap:5px}
.dot{width:6px;height:6px;border-radius:50%;background:var(--white);display:inline-block}
.wordmark{font-weight:800;color:var(--blue);letter-spacing:.3px}
.site-top{right:26px;top:20px;color:var(--white);font-size:9px}
.front-title{left:364px;top:245px;color:var(--white);font-weight:800;font-size:26px;line-height:.98}
.front-tag{left:364px;top:333px;color:var(--white);font-size:12.5px;line-height:1.38}
.divider{left:336px;top:0;width:1px;height:229px;background:rgba(255,255,255,.35)}

/* inside pages */
.page{position:absolute;width:307px;height:434px;top:682px;overflow:hidden;background:linear-gradient(165deg,#dbe9f5 0%,#eef4fa 40%,#f4eaea 70%,#e4eef7 100%)}
.page-head{left:0;top:0;width:100%;height:23px;background:rgba(255,255,255,.6);font-size:4.6px;color:#444}
.page-head .l{position:absolute;left:23px;top:16px}
.page-head .r{position:absolute;right:22px;top:14px;font-size:6px}
.foot-num{position:absolute;left:26px;top:408px;width:10px;height:9px;border:.7px solid var(--deep);background:var(--white);font-size:4.6px;font-weight:700;text-align:center;line-height:8px}
.foot-line{position:absolute;left:0;top:412px;width:116px;height:.7px;background:var(--sky)}
.foot-mark{position:absolute;right:19px;top:405px;font-size:10px}
.art{position:absolute;border-radius:8px}
.art-light{background:linear-gradient(150deg,#e8f1f8 0%,#cadeef 35%,#7badd7 75%,#4f8fcc 100%)}
.art-mid{background:linear-gradient(150deg,#cadeef 0%,#7badd7 45%,#1480c4 80%,#1656a8 100%)}
.tag{position:absolute;background:var(--blue);color:var(--white);font-weight:600;font-size:6px;padding:2px 6px;border-radius:0 6px 6px 0;white-space:nowrap}
.bar{position:absolute;background:var(--slate);color:var(--white);font-size:5px;line-height:1.45;padding:8px 6px 3px}
.item{position:absolute;display:flex;gap:5px;width:140px}
.item .ic{flex:0 0 11px;width:11px;height:11px;color:var(--slate);margin-top:1px}
.item b{display:block;color:var(--deep);font-weight:600;font-size:5px}
.item span{display:block;font-size:4.8px;line-height:1.35;color:#444}
.sep{position:absolute;height:0;border-top:.5px dashed #9aa}

.about{left:24px;top:41px;width:283px;height:77px;background:var(--deep);color:var(--white);padding:10px 0 0 11px}
.about h3{font-size:8.5px;font-weight:600;margin:0 0 4px 24px}
.about p{font-size:5px;line-height:1.45;width:155px;text-align:justify}
.quote{position:absolute;left:11px;top:7px;width:17px;height:11px}
.svc-intro{left:24px;top:141px;width:69px;height:99px;background:var(--slate);color:var(--white);font-size:5.2px;line-height:1.35;padding:21px 6px 0}
.svc-arrow{left:93px;top:150px;width:0;height:0;border-top:6px solid transparent;border-bottom:6px solid transparent;border-left:6px solid var(--slate)}
.card{position:absolute;width:90px;height:49px;color:var(--white);padding:5px 5px 0;font-size:4.3px;line-height:1.35}
.card .ci{display:block;width:11px;height:11px;color:var(--white);margin-bottom:4px}
.card b{display:block;font-weight:600}
.card.dark{background:var(--slate)}
.card.blue{background:var(--blue)}

.why-line{left:43px;top:60px;height:175px;border-left:.8px dotted var(--slate)}
.why-dot{position:absolute;left:28px;width:31px;height:31px;border-radius:50%;border:1px solid var(--white);box-shadow:0 0 0 1px #9ab;display:flex;align-items:center;justify-content:center;color:var(--white)}
.why-dot svg{width:15px;height:15px}
.why-dot.dark{background:var(--slate)}
.why-dot.blue{background:var(--blue)}
.why{position:absolute;left:69px;width:228px}
.why b{display:block;color:var(--deep);font-weight:600;font-size:5.8px;margin-bottom:2px}
.why span{display:block;font-size:4.9px;line-height:1.45;color:#444}
</style>
</head>
<body>

<svg class="icon-defs" aria-hidden="true">
  <defs>
    <symbol id="i-monitor" viewBox="0 0 20 20"><g fill="none" stroke="currentColor" stroke-width="1.5" stroke-linecap="round"><rect x="2" y="3" width="16" height="11" rx="1"/><path d="M10 14v3M6 17h8M6 10l2.5-3 2 2 3.5-3.5"/></g></symbol>
    <symbol id="i-headset" viewBox="0 0 20 20"><g fill="none" stroke="currentColor" stroke-width="1.5" stroke-linecap="round"><path d="M4 12v-2a6 6 0 0 1 12 0v2"/><rect x="3" y="11" width="3" height="5" rx="1"/><rect x="14" y="11" width="3" height="5" rx="1"/><path d="M16 16c0 1.5-2 2-4 2"/></g></symbol>
    <symbol id="i-gear" viewBox="0 0 20 20"><g fill="none" stroke="currentColor"><circle cx="10" cy="10" r="5.5" stroke-width="2.6" stroke-dasharray="2.2 1.6"/><circle cx="10" cy="10" r="2.3" stroke-width="1.4"/></g></symbol>
    <symbol id="i-list" viewBox="0 0 20 20"><g fill="none" stroke="currentColor" stroke-width="1.5" stroke-linecap="round"><rect x="4" y="2.5" width="12" height="15" rx="1"/><path d="M7 7h6M7 10h6M7 13h4"/></g></symbol>
    <symbol id="i-cloud" viewBox="0 0 20 20"><g fill="none" stroke="currentColor" stroke-width="1.5" stroke-linejoin="round"><path d="M6 15h9a3.5 3.5 0 0 0 0-7 5 5 0 0 0-9.5 1A3 3 0 0 0 6 15z"/><path d="M10 9v4M8.3 10.7L10 9l1.7 1.7"/></g></symbol>
    <symbol id="i-server" viewBox="0 0 20 20"><g fill="none" stroke="currentColor" stroke-width="1.5"><rect x="3" y="3" width="14" height="5.5" rx="1"/><rect x="3" y="11.5" width="14" height="5.5" rx="1"/><path d="M6 5.75h1M6 14.25h1M10 5.75h4M10 14.25h4"/></g></symbol>
    <symbol id="i-refresh" viewBox="0 0 20 20"><g fill="none" stroke="currentColor" stroke-width="1.5" stroke-linecap="round"><path d="M16 8a6.5 6.5 0 0 0-11.5-1.5M4 12a6.5 6.5 0 0 0 11.5 1.5"/><path d="M4 3v3.5h3.5M16 17v-3.5h-3.5"/></g></symbol>
    <symbol id="i-apps" viewBox="0 0 20 20"><g fill="none" stroke="currentColor" stroke-width="1.5"><rect x="3" y="3" width="6" height="6" rx="1"/><rect x="11" y="3" width="6" height="6" rx="1"/><rect x="3" y="11" width="6" height="6" rx="1"/><circle cx="14" cy="14" r="3"/></g></symbol>
    <symbol id="i-shield" viewBox="0 0 20 20"><g fill="none" stroke="currentColor" stroke-width="1.5" stroke-linejoin="round" stroke-linecap="round"><path d="M10 2l7 3v5c0 4-3 7-7 8-4-1-7-4-7-8V5z"/><path d="M7 10l2 2 4-4"/></g></symbol>
    <symbol id="i-search" viewBox="0 0 20 20"><g fill="none" stroke="currentColor" stroke-width="1.5" stroke-linecap="round"><circle cx="8.5" cy="8.5" r="5"/><path d="M12.3 12.3L17 17"/></g></symbol>
    <symbol id="i-lock" viewBox="0 0 20 20"><g fill="none" stroke="currentColor" stroke-width="1.5"><rect x="4" y="9" width="12" height="8.5" rx="1"/><path d="M6.5 9V6.5a3.5 3.5 0 0 1 7 0V9M10 12v2.5"/></g></symbol>
    <symbol id="i-check" viewBox="0 0 20 20"><g fill="none" stroke="currentColor" stroke-width="1.5" stroke-linecap="round" stroke-linejoin="round"><rect x="3" y="3" width="14" height="14" rx="2"/><path d="M6.5 10l2.5 2.5 4.5-5"/></g></symbol>
    <symbol id="i-target" viewBox="0 0 20 20"><g fill="none" stroke="currentColor" stroke-width="1.5"><circle cx="10" cy="10" r="7"/><circle cx="10" cy="10" r="4"/><circle cx="10" cy="10" r="1" fill="currentColor"/></g></symbol>
    <symbol id="i-chart" viewBox="0 0 20 20"><g fill="none" stroke="currentColor" stroke-width="1.5" stroke-linecap="round"><path d="M3 17h14M5 17v-4M9 17V9M13 17v-6M17 17V5"/></g></symbol>
    <symbol id="i-clipboard" viewBox="0 0 20 20"><g fill="none" stroke="currentColor" stroke-width="1.5" stroke-linecap="round"><rect x="4" y="4" width="12" height="14" rx="1"/><path d="M8 3h4v2.5H8zM7 10l2 2 4-4"/></g></symbol>
    <symbol id="i-pointer" viewBox="0 0 20 20"><g fill="none" stroke="currentColor" stroke-width="1.5" stroke-linejoin="round"><path d="M6 3l9 7-4 1 2.5 5-2 1-2.5-5-3 3z"/></g></symbol>
    <symbol id="i-person" viewBox="0 0 20 20"><g fill="none" stroke="currentColor" stroke-width="1.5"><circle cx="10" cy="7" r="3.5"/><path d="M3.5 17.5a6.5 6.5 0 0 1 13 0"/></g></symbol>
    <symbol id="i-layers" viewBox="0 0 20 20"><g fill="none" stroke="currentColor" stroke-width="1.5" stroke-linejoin="round"><path d="M10 3l7 3.5-7 3.5-7-3.5z"/><path d="M3 10l7 3.5 7-3.5M3 13.5l7 3.5 7-3.5"/></g></symbol>
  </defs>
</svg>

<div class="label" style="left:438px">BACK</div>
<div class="label" style="left:770px">FRONT</div>
<div class="mount" style="left:265px;top:101px;width:693px;height:460px"></div>

<section class="spread">
  <div class="photo back-photo" role="img" aria-label="Photograph of a dark server room with glowing rack aisles"></div>
  <div class="photo front-photo" role="img" aria-label="Illustration of a glowing blue city skyline floating on a cloud platform"></div>
  <div class="abs divider"></div>

  <div class="abs get-touch">
    <h3>Get in Touch</h3>
    <p>Discover how Korvalith can transform your IT landscape and drive your business forward. Contact us today to learn more about our services and how we can help you achieve your goals.</p>
  </div>

  <div class="abs contact-band">
    <h4>Contact Us</h4>
    <ul>
      <li><svg viewBox="0 0 10 10"><circle cx="5" cy="5" r="4.3" fill="none" stroke="#fff"/><path d="M1 5h8M5 1c-2 2.5-2 5.5 0 8M5 1c2 2.5 2 5.5 0 8" fill="none" stroke="#fff" stroke-width=".7"/></svg>www.korvalith.co.uk</li>
      <li><svg viewBox="0 0 10 10"><rect x="1" y="2" width="8" height="6" fill="#fff"/><path d="M1 2l4 3.3L9 2" fill="none" stroke="#1480c4" stroke-width=".8"/></svg>info@korvalith.co.uk</li>
      <li><svg viewBox="0 0 10 10"><path d="M1 3.5C1 2 3 1 5 1s4 1 4 2.5H7L6.5 3h-3L3 3.5zM2.5 5h5l1 4h-7z" fill="#fff"/></svg>+44 20 7946 0312</li>
      <li><svg viewBox="0 0 10 10"><path d="M5 1l4.2 4H8v4H2V5H.8z" fill="#fff"/></svg>48 Lumen Street, Harbourgate Park, London, UK</li>
    </ul>
  </div>

  <div class="abs follow-band">
    <h4>Follow Us</h4>
    <p>Stay updated with the latest news and updates from Korvalith:</p>
    <ul>
      <li><i class="dot"></i>https://www.connectly.com/korvalithltd</li>
      <li><i class="dot"></i>https://www.chirper.com/KorvalithLTD</li>
      <li><i class="dot"></i>http://www.proflink.com/company/korvalith?ref=top_nav_home</li>
    </ul>
  </div>

  <svg class="abs" style="left:336px;top:229px" width="334" height="160" viewBox="0 0 334 160">
    <rect x="0" y="0" width="334" height="87" fill="var(--blue)"/>
    <path d="M0 89H180C260 89 318 50 334 -25V20C318 100 270 158 190 158H0Z" fill="var(--deep)"/>
    <path d="M0 88H180C260 88 318 49 334 -26" fill="none" stroke="#fff" stroke-width="1.6"/>
  </svg>

  <div class="abs site-top">korvalith.co.uk</div>
  <div class="abs front-title">KORVALITH IT<br>SERVICES</div>
  <div class="abs front-tag">Empowering Your Business with<br>Cutting-Edge IT Solutions</div>

  <div class="abs wordmark" style="left:28px;top:404px;font-size:14px">KORVALITH</div>
  <div class="abs wordmark" style="right:28px;top:404px;font-size:14px">KORVALITH</div>
</section>

<div class="label" style="left:277px;top:623px">iNSIDE 1</div>
<div class="label" style="left:588px;top:623px">iNSIDE 2</div>
<div class="label" style="left:915px;top:623px">iNSIDE 3</div>
<div class="mount" style="left:107px;top:671px;width:984px;height:459px"></div>

<!-- Inside 1 -->
<section class="page" style="left:118px">
  <div class="abs page-head"><span class="l">Korvalith IT Services Brochure</span><span class="r">korvalith.co.uk</span></div>

  <div class="abs about">
    <svg class="quote" viewBox="0 0 17 11"><path d="M0 11V5L3 0h3L4 4h3v7zM9 11V5l3-5h3l-2 4h3v7z" fill="#fff"/></svg>
    <h3>About Korvalith</h3>
    <p>At Korvalith, we are dedicated to providing top-tier IT services that drive efficiency, innovation, and growth for your business. With a commitment to excellence and a team of highly skilled professionals, we offer a comprehensive suite of solutions tailored to meet the unique needs of our clients.</p>
  </div>
  <div class="art art-light" style="left:198px;top:32px;width:94px;height:92px" role="img" aria-label="Illustration of a team working around a large laptop with charts and coins"></div>

  <div class="abs svc-intro">Our Managed IT Services provide proactive monitoring and management of your IT infrastructure, ensuring maximum uptime and reliability. We offer:</div>
  <div class="abs svc-arrow"></div>
  <div class="tag" style="left:24px;top:137px">OUR SERVICES</div>
  <div class="card dark" style="left:104px;top:140px"><svg class="ci"><use href="#i-monitor"/></svg><b>24/7 Network Monitoring:</b>Continuous monitoring to detect and resolve issues before they impact your business.</div>
  <div class="card blue" style="left:197px;top:140px"><svg class="ci"><use href="#i-headset"/></svg><b>Helpdesk Support:</b>Responsive and knowledgeable support team available round the clock.</div>
  <div class="card blue" style="left:104px;top:193px"><svg class="ci"><use href="#i-gear"/></svg><b>Patch Management:</b>Regular updates and patches to keep your systems secure and up-to-date.</div>
  <div class="card dark" style="left:197px;top:193px"><svg class="ci"><use href="#i-list"/></svg><b>IT Asset Management:</b>Comprehensive tracking and management of your IT assets.</div>

  <div class="bar" style="left:24px;top:261px;width:181px;height:29px">Embrace the power of the cloud with our scalable and secure cloud solutions. Our offerings include:</div>
  <div class="tag" style="left:24px;top:256px">CLOUD SOLUTIONS</div>
  <div class="art art-mid" style="left:208px;top:262px;width:84px;height:88px" role="img" aria-label="Illustration of layered cloud security screens and padlocks"></div>

  <div class="item" style="left:31px;top:301px;width:170px"><svg class="ic"><use href="#i-cloud"/></svg><div><b>Cloud Migration:</b><span>Seamless transition of your applications and data to the cloud.</span></div></div>
  <div class="sep" style="left:31px;top:321px;width:170px"></div>
  <div class="item" style="left:31px;top:329px;width:170px"><svg class="ic"><use href="#i-server"/></svg><div><b>Cloud Hosting:</b><span>Reliable and scalable hosting solutions to meet your growing needs.</span></div></div>
  <div class="sep" style="left:31px;top:350px;width:170px"></div>
  <div class="item" style="left:31px;top:358px;width:240px"><svg class="ic"><use href="#i-refresh"/></svg><div><b>Backup and Disaster Recovery:</b><span>Robust backup and recovery solutions to ensure business continuity.</span></div></div>
  <div class="item" style="left:31px;top:381px;width:240px"><svg class="ic"><use href="#i-apps"/></svg><div><b>Software as a Service (SaaS):</b><span>Access to the latest software applications without the hassle of maintenance.</span></div></div>

  <div class="foot-line"></div><div class="foot-num">01</div>
  <div class="foot-mark wordmark">KORVALITH</div>
</section>

<!-- Inside 2 -->
<section class="page" style="left:444px">
  <div class="abs page-head"><span class="l">Korvalith IT Services Brochure</span><span class="r">korvalith.co.uk</span></div>

  <div class="art art-light" style="left:12px;top:48px;width:122px;height:130px" role="img" aria-label="Isometric illustration of people at desks linked to a cloud shield and server racks"></div>
  <div class="bar" style="left:140px;top:57px;width:167px;height:22px">Protect your business from evolving threats with our comprehensive cybersecurity services. We offer:</div>
  <div class="tag" style="left:138px;top:50px">CYBERSECURITY</div>
  <div class="item" style="left:150px;top:87px;width:150px"><svg class="ic"><use href="#i-shield"/></svg><div><b>Threat Detection and Response:</b><span>Advanced threat monitoring and response to safeguard your data.</span></div></div>
  <div class="sep" style="left:150px;top:110px;width:150px"></div>
  <div class="item" style="left:150px;top:116px;width:150px"><svg class="ic"><use href="#i-search"/></svg><div><b>Security Audits and Assessments:</b><span>Thorough evaluations to identify and mitigate vulnerabilities.</span></div></div>
  <div class="sep" style="left:150px;top:139px;width:150px"></div>
  <div class="item" style="left:150px;top:145px;width:150px"><svg class="ic"><use href="#i-lock"/></svg><div><b>Endpoint Protection:</b><span>Robust security solutions for all your devices.</span></div></div>
  <div class="sep" style="left:150px;top:162px;width:150px"></div>
  <div class="item" style="left:150px;top:168px;width:150px"><svg class="ic"><use href="#i-check"/></svg><div><b>Compliance and Regulatory Services:</b><span>Ensure adherence to industry standards and regulations.</span></div></div>

  <div class="art art-mid" style="left:12px;top:220px;width:110px;height:112px" role="img" aria-label="Illustration of a consultant beside large monitors with code and gears"></div>
  <div class="bar" style="left:127px;top:231px;width:180px;height:24px">Leverage our expertise to drive your IT strategy and achieve your business goals. Our consulting services include:</div>
  <div class="tag" style="left:127px;top:224px">IT CONSULTING</div>
  <div class="item" style="left:134px;top:264px;width:160px"><svg class="ic"><use href="#i-target"/></svg><div><b>IT Strategy and Planning:</b><span>Strategic guidance to align your IT initiatives with your business objectives.</span></div></div>
  <div class="sep" style="left:134px;top:286px;width:160px"></div>
  <div class="item" style="left:134px;top:292px;width:160px"><svg class="ic"><use href="#i-search"/></svg><div><b>Technology Assessments:</b><span>In-depth evaluations to optimize your IT infrastructure.</span></div></div>
  <div class="sep" style="left:134px;top:315px;width:160px"></div>
  <div class="item" style="left:134px;top:321px;width:160px"><svg class="ic"><use href="#i-clipboard"/></svg><div><b>Project Management:</b><span>Expert management of IT projects from inception to completion.</span></div></div>
  <div class="item" style="left:134px;top:351px;width:160px"><svg class="ic"><use href="#i-chart"/></svg><div><b>Business Continuity Planning:</b><span>Strategies to ensure your business remains operational during disruptions.</span></div></div>

  <div class="foot-line"></div><div class="foot-num">02</div>
  <div class="foot-mark wordmark">KORVALITH</div>
</section>

<!-- Inside 3 -->
<section class="page" style="left:770px">
  <div class="abs page-head"><span class="l">Korvalith IT Services Brochure</span><span class="r">korvalith.co.uk</span></div>

  <div class="abs" style="left:28px;top:40px;width:1px;height:11px;background:var(--blue)"></div>
  <div class="tag" style="left:29px;top:40px;padding:2px 8px">Why Choose Korvalith?</div>

  <div class="abs why-line"></div>
  <div class="abs" style="left:41px;top:58px;width:4px;height:4px;border-radius:50%;background:var(--slate)"></div>
  <div class="abs" style="left:41px;top:233px;width:4px;height:4px;border-radius:50%;background:var(--slate)"></div>
  <div class="why-dot dark" style="top:68px"><svg><use href="#i-pointer"/></svg></div>
  <div class="why-dot blue" style="top:108px"><svg><use href="#i-person"/></svg></div>
  <div class="why-dot dark" style="top:150px"><svg><use href="#i-headset"/></svg></div>
  <div class="why-dot blue" style="top:191px"><svg><use href="#i-layers"/></svg></div>

  <div class="why" style="top:69px"><b>Why Choose Korvalith?</b><span>With years of experience in the IT industry, our team possesses the knowledge and skills to tackle any challenge. We stay abreast of the latest technological advancements to provide you with cutting-edge solutions.</span></div>
  <div class="why" style="top:112px"><b>Customer-Centric Approach</b><span>We prioritize our clients' needs and work closely with them to deliver customized solutions that drive success. Our client-centric approach ensures that we are always aligned with your business goals.</span></div>
  <div class="why" style="top:153px"><b>Proactive Support</b><span>Our proactive support model ensures that potential issues are identified and resolved before they can impact your operations. We are committed to maintaining the highest levels of service availability and performance.</span></div>
  <div class="why" style="top:197px"><b>Comprehensive Solutions</b><span>From managed services to cybersecurity, we offer a comprehensive suite of IT solutions designed to meet the diverse needs of your business. Our holistic approach ensures that all aspects of your IT infrastructure are covered.</span></div>

  <div class="art art-light" style="left:14px;top:244px;width:279px;height:152px" role="img" aria-label="Isometric illustration of a data centre platform with people working at screens"></div>

  <div class="foot-line"></div><div class="foot-num">03</div>
  <div class="foot-mark wordmark">KORVALITH</div>
</section>

</body>
</html>
```